Voltbrisk package design alternate designs & color themes

We want to see different options from multiple artists for our Brand Voltbrisk. We are an electronic accessories company that sell everything from camera accessories to mobile device accessories. We are looking for a simple yet professional design for our packaging. Attached is one example, however we are looking for your creativity. Please use any colors / design theme that you see fit for an electronics accessory company, that blend well with the current logo.
Electronic Accessories

```html
<!DOCTYPE html>
<html lang="en">
<head>
<meta charset="utf-8">
<title>Voltbrisk Sound Support Headphones Stand Packaging</title>
<link rel="stylesheet" href="https://fonts.googleapis.com/css2?family=Montserrat:ital,wght@0,400;0,600;0,800;1,400&display=swap">
<style>
  :root {
    --bg: #eeeeee;
    --ink: #111111;
    --lid: #1a1a1a;
    --white: #ffffff;
    --green: #6abf2a;
    --green-deep: #3f9a12;
    --green-soft: #8cd155;
    --grey-band: #d6d6d6;
    --photo-dark: #2a2a2a;
    --photo-light: #f2f2f2;
  }
  * { margin: 0; padding: 0; box-sizing: border-box; }
  html, body { width: 1200px; height: 1200px; overflow: hidden; }
  body {
    background: var(--bg);
    font-family: "Montserrat", sans-serif;
    color: var(--ink);
    position: relative;
  }
  .dieline { position: absolute; left: 110px; top: 140px; width: 980px; height: 920px; }

  .panel-top {
    position: absolute; left: 0; top: 0; width: 760px; height: 160px;
    background: var(--lid);
    display: flex; align-items: center; justify-content: center;
  }
  .panel-top .brand-name {
    color: var(--white); font-weight: 800; font-size: 64px; letter-spacing: 1px;
  }

  .panel-front {
    position: absolute; left: 0; top: 160px; width: 760px; height: 760px;
    background: var(--white); overflow: hidden;
  }
  .front-brand {
    position: absolute; left: 40px; top: 36px;
    color: var(--green); font-weight: 800; font-size: 30px;
  }
  .product-photo {
    position: absolute; left: 150px; top: 120px; width: 430px; height: 470px;
    background: radial-gradient(ellipse at 50% 45%, var(--photo-dark) 0%, #555 45%, var(--photo-light) 75%);
    border-radius: 50% 50% 12px 12px / 40% 40% 12px 12px;
  }
  .badge {
    position: absolute; left: 560px; top: 250px; width: 120px; height: 120px;
    border-radius: 50%; background: var(--green-soft);
    display: flex; align-items: center; justify-content: center; text-align: center;
    font-size: 12px; font-weight: 600; line-height: 1.3; color: var(--ink);
  }
  .title-band {
    position: absolute; left: 0; top: 600px; width: 560px; height: 100px;
    background: linear-gradient(90deg, var(--grey-band), var(--white));
    padding: 18px 40px;
  }
  .title-band .line-strong { font-weight: 800; font-size: 30px; line-height: 1.1; }
  .title-band .line-light { font-weight: 400; font-size: 30px; line-height: 1.1; }
  .front-base {
    position: absolute; left: 0; bottom: 0; width: 100%; height: 60px;
    background: linear-gradient(90deg, var(--white), var(--green) 70%);
  }

  .panel-side {
    position: absolute; left: 760px; top: 160px; width: 220px; height: 760px;
    background: linear-gradient(180deg, var(--green) 0%, var(--green-deep) 100%);
    padding: 40px 22px; color: var(--white);
  }
  .panel-side p {
    font-style: italic; font-size: 12px; line-height: 1.5; margin-bottom: 12px;
  }
</style>
</head>
<body>
  <main class="dieline">
    <section class="panel-top">
      <span class="brand-name">Voltbrisk</span>
    </section>

    <section class="panel-front">
      <span class="front-brand">Voltbrisk</span>
      <div class="product-photo" role="img" aria-label="Product photo of black over-ear headphones resting on an aluminum stand"></div>
      <div class="badge">HIGH GRADE<br>LIGHTWEIGHT<br>ALUMINUM</div>
      <div class="title-band">
        <div class="line-strong">SOUND SUPPORT</div>
        <div class="line-light">HEADPHONES STAND</div>
      </div>
      <div class="front-base"></div>
    </section>

    <section class="panel-side">
      <p>Keep your headphones safe and ready with a sturdy stand built from lightweight aluminum. The weighted base stays put on any desk while the curved cradle protects the headband from stretching over time.</p>
      <p>Soft padding on the top rail prevents scratches, and the slim column saves space in small setups. Fits most over ear and on ear models.</p>
      <p>Simple to assemble in seconds with no tools needed. Wipe clean with a dry cloth.</p>
    </section>
  </main>
</body>
</html>
```